Fizz's Shed & Grill Burger Restaurant Website - HomePage Only PSD

I need a website design for a restaurant called "Fizz's Shed and Grill" featuring burgers, wings, beer, live music, trivia, and more. I have several images of the restaurant and they already have their logo files created (see attached). I want some type of wood background and integrate the silver tin. This needs to be a modern, hip and fun type design. Design must incorporate these attached graphics.

UPDATE - just added a few more images of things I really like to be incorporated into my designs.
Updates

Industry/Entity Type

Burger Restaurant

Number of Pages Required

1 page

Font styles to use
Sans Serif

Requirements
Must have
• Restaurant/Bar theme with integration of existing logo and the red wood look.
Nice to have
• - Modern Fun appearance
• - Use Pelko Fonts

```html
<!DOCTYPE html>
<html lang="en">
<head>
<meta charset="utf-8">
<title>Fizz's Shed and Grill</title>
<link rel="stylesheet" href="https://fonts.googleapis.com/css2?family=Merienda:wght@700&family=Oswald:wght@400;500&family=PT+Sans:wght@400;700&display=swap">
<style>
:root{
  --orange:#f28c0f;
  --orange-dark:#c96d05;
  --dark:#2d2d2d;
  --darker:#161412;
  --paper:#f1f1f0;
  --paper-line:#e6e6e4;
  --text:#4a4a4a;
  --muted:#9a9a9a;
  --white:#ffffff;
}
*{margin:0;padding:0;box-sizing:border-box}
html,body{width:1200px;height:2582px;overflow:hidden}
body{font-family:"PT Sans",sans-serif;color:var(--text);background:var(--paper)}
.page{position:relative;width:1200px;height:2582px;overflow:hidden;
  background:repeating-linear-gradient(90deg,var(--paper) 0 38px,var(--paper-line) 38px 40px)}
.abs{position:absolute}

/* header */
.topbar{left:0;top:0;width:1200px;height:170px}
.info{display:flex;align-items:flex-start;gap:16px}
.info .ico{width:42px;height:42px;border:2px solid var(--orange);border-radius:50%;display:flex;align-items:center;justify-content:center}
.info h4{font-family:"Merienda",cursive;color:var(--orange);font-size:22px;line-height:1.1}
.info p{font-family:"Merienda",cursive;color:var(--orange);font-size:17px;margin-top:8px}
.ribbon{left:0;top:134px;width:1200px;height:70px}
.nav{left:77px;top:134px;width:1042px;height:52px;display:flex;align-items:center;font-family:"Oswald",sans-serif;font-size:16px;color:var(--white);text-transform:uppercase}
.nav a{position:absolute;color:var(--white);text-decoration:none}
.brand-badge{left:525px;top:42px;width:156px;height:156px;border-radius:50%;background:var(--white);border:5px solid #222;display:flex;align-items:center;justify-content:center;text-align:center;font-family:"PT Sans",sans-serif;font-weight:700;font-size:19px;color:#222;line-height:1.2;padding:14px}

/* hero */
.hero{left:0;top:170px;width:1200px;height:519px;background:radial-gradient(ellipse at 50% 40%,#3a3a3a,var(--dark) 70%,#222)}
.hero-mark{left:176px;top:297px;width:130px;height:130px;border-radius:50%;border:3px solid var(--white);display:flex;align-items:center;justify-content:center;text-align:center;color:var(--white);font-weight:700;font-size:16px;line-height:1.2;padding:12px}
.hero-title{left:114px;top:450px;font-size:23px;letter-spacing:1px;color:var(--white);font-weight:400}
.hero-text{left:110px;top:488px;width:290px;text-align:center;font-size:14px;line-height:26px;color:#a9a9a9}
.btn-dark{left:158px;top:561px;width:166px;height:42px;border:1px solid #777;background:#222;color:var(--white);font-size:16px;display:flex;align-items:center;justify-content:center}
.photo-back{background:var(--white);box-shadow:0 4px 10px rgba(0,0,0,.5)}
.photo{left:568px;top:285px;width:518px;height:280px;background:linear-gradient(135deg,#6b3b22,#3c2013 55%,#8c2d1a);border:8px solid var(--white)}
.round-arrow{width:28px;height:28px;border-radius:50%;border:2px solid #ccc;background:#555;display:flex;align-items:center;justify-content:center}

/* section titles */
.sec-title{height:56px;background:var(--white);box-shadow:0 3px 4px rgba(0,0,0,.15);display:flex;align-items:center;justify-content:center;font-family:"Merienda",cursive;font-size:30px;letter-spacing:1px;color:#333;text-transform:uppercase}
.sec-title span{color:var(--orange)}
.rule{height:2px;background:var(--orange);width:40px}
.divider{display:flex;align-items:center;gap:8px;justify-content:center}
.divider i{width:12px;height:12px;border-radius:50%;background:var(--orange);display:block}
.lead{font-size:16px;color:#888;text-align:center;width:1200px;left:0}

/* recipes */
.recipe{width:234px;height:269px;background:linear-gradient(160deg,#c77a2a,#7a3a12);box-shadow:0 14px 12px -10px rgba(0,0,0,.35)}
.recipe .frame{position:absolute;left:8px;top:8px;right:8px;bottom:8px;border:2px solid var(--white)}
.recipe .label{position:absolute;left:8px;top:9px;right:8px;height:44px;background:#111;color:var(--white);font-size:16px;display:flex;align-items:center;justify-content:center}
.recipe .more{position:absolute;left:79px;bottom:-38px;width:76px;height:76px;border-radius:50%;background:var(--orange);border:4px solid var(--white);clip-path:inset(0 0 50% 0);}
.recipe .more-t{position:absolute;left:0;width:234px;bottom:-12px;text-align:center;font-size:12px;color:var(--white)}
.side-btn{width:30px;height:54px;background:#777;display:flex;align-items:center;justify-content:center}

/* events */
.events{left:0;top:1269px;width:1200px;height:344px;background:linear-gradient(180deg,#1e1a16,#0f0d0b 60%,#1a1511)}
.events h2{position:absolute;left:0;width:1200px;top:36px;text-align:center;font-family:"Merienda",cursive;font-size:30px;color:var(--white);letter-spacing:1px}
.events h2 span{color:var(--orange)}
.events .sub{position:absolute;left:0;width:1200px;top:88px;text-align:center;font-style:italic;color:#ddd;font-size:13px}
.event{width:330px;height:80px}
.date{position:absolute;left:0;top:0;width:77px;height:75px;border:1px solid #ddd;color:var(--white);text-align:center}
.date b{display:block;font-size:24px;color:var(--orange);margin-top:8px}
.date small{font-size:13px}
.event h5{position:absolute;left:98px;top:10px;color:var(--orange);font-size:13px;font-weight:700;white-space:nowrap}
.event p{position:absolute;left:98px;color:#ddd;font-size:12px;display:flex;align-items:center;gap:8px;white-space:nowrap}
.btn-outline{left:499px;top:260px;width:207px;height:43px;border:2px solid #ddd;color:var(--white);font-size:13px;font-weight:700;display:flex;align-items:center;justify-content:center}

/* menu */
.dish{width:233px;height:231px;background:var(--white);border:1px solid #e3e3e3}
.dish .img{position:absolute;left:40px;top:40px;width:152px;height:140px;border-radius:10px}
.dish-meta{width:233px;text-align:center}
.dish-meta h6{font-size:16px;font-weight:400;color:#444}
.dish-meta em{display:block;font-size:11px;color:#aaa;margin-top:6px}
.dish-meta .price{margin-top:6px;font-size:17px;color:var(--orange)}
.dish-meta .price s{font-size:12px;color:#999;margin-right:12px}
.order{width:124px;height:32px;border:2px solid var(--orange);color:var(--orange);font-size:13px;display:flex;align-items:center;justify-content:center;background:var(--white)}

/* footer */
.footer{left:0;top:2199px;width:1200px;height:383px;background:linear-gradient(180deg,#1d1916,#120f0d)}
.footer h3{position:absolute;font-size:15px;font-weight:700;color:var(--white);text-transform:uppercase}
.c-item{position:absolute;left:100px;display:flex;gap:16px}
.c-item h6{color:var(--orange);font-size:16px;font-weight:400}
.c-item p{color:#ccc;font-size:13px;line-height:22px;margin-top:4px}
.hours{position:absolute;left:385px;width:320px;font-size:13px;color:#ddd}
.hours div{position:absolute;left:0;width:320px;display:flex;align-items:center}
.hours .line{flex:1;height:1px;background:#ccc;margin:0 12px}
.map{left:778px;top:67px;width:320px;height:193px;background:linear-gradient(135deg,#e8e5df,#d9d6cd 50%,#bcd3ea);border:3px solid var(--white)}
.foot-rule{left:100px;top:318px;width:1000px;height:1px;background:#555}
.copy{left:100px;top:342px;font-size:12px;color:#ddd}
.social{width:30px;height:30px;border-radius:50%;border:1px solid #ddd}
.edge{left:0;width:1200px;height:10px}
</style>
</head>
<body>
<div class="page">

  <!-- header -->
  <header class="abs topbar">
    <div class="abs info" style="left:99px;top:40px">
      <div class="ico"><svg width="20" height="20" viewBox="0 0 24 24"><path d="M6.6 10.8a15 15 0 0 0 6.6 6.6l2.2-2.2c.3-.3.7-.4 1-.2 1.1.4 2.3.6 3.6.6.6 0 1 .4 1 1V20c0 .6-.4 1-1 1A17 17 0 0 1 3 4c0-.6.4-1 1-1h3.5c.6 0 1 .4 1 1 0 1.3.2 2.5.6 3.6.1.3 0 .7-.2 1z" fill="#f28c0f"/></svg></div>
      <div><h4>Call Us Now!</h4><p>+123 4567 890</p></div>
    </div>
    <div class="abs info" style="left:890px;top:40px">
      <div class="ico"><svg width="22" height="22" viewBox="0 0 24 24"><circle cx="12" cy="12" r="9" fill="none" stroke="#f28c0f" stroke-width="2"/><path d="M12 7v5l3 2" stroke="#f28c0f" stroke-width="2" fill="none"/></svg></div>
      <div><h4>Opening hours</h4><p>8AM - 9PM</p></div>
    </div>
  </header>

  <svg class="abs ribbon" viewBox="0 0 1200 70" width="1200" height="70">
    <polygon points="0,14 77,14 77,66 0,66 24,40" fill="#d77a08"/>
    <polygon points="1200,14 1123,14 1123,66 1200,66 1176,40" fill="#d77a08"/>
    <polygon points="77,52 100,52 100,66" fill="#8a4c02"/>
    <polygon points="1123,52 1100,52 1100,66" fill="#8a4c02"/>
    <rect x="77" y="0" width="1046" height="52" fill="#f28c0f"/>
  </svg>
  <nav class="abs nav">
    <a style="left:88px">Home</a>
    <a style="left:174px">About</a>
    <a style="left:267px">Burgers</a>
    <a style="left:378px">Wings</a>
    <a style="left:612px">Beer</a>
    <a style="left:694px">Live Music</a>
    <a style="left:815px">Trivia</a>
    <a style="left:908px">Contact Us</a>
  </nav>
  <div class="abs brand-badge">Fizz's Shed and Grill</div>

  <!-- hero -->
  <section class="abs hero"></section>
  <div class="abs hero-mark">Fizz's Shed and Grill</div>
  <h1 class="abs hero-title">FIZZ'S SHED AND GRILL</h1>
  <p class="abs hero-text">Perspiciatis unde omnis iste natus error sit voluptatem accusantium doloremque</p>
  <div class="abs btn-dark">Book Now !</div>
  <div class="abs photo-back" style="left:530px;top:252px;width:548px;height:318px;transform:rotate(-2deg)"></div>
  <div class="abs photo-back" style="left:545px;top:265px;width:548px;height:310px;transform:rotate(-1deg)"></div>
  <div class="abs photo" role="img" aria-label="Grilled steaks with salad and cherry tomatoes"></div>
  <div class="abs round-arrow" style="left:792px;top:609px"><svg width="12" height="12" viewBox="0 0 12 12"><path d="M8 2 3 6l5 4" stroke="#fff" stroke-width="2" fill="none"/></svg></div>
  <div class="abs round-arrow" style="left:850px;top:609px"><svg width="12" height="12" viewBox="0 0 12 12"><path d="M4 2l5 4-5 4" stroke="#fff" stroke-width="2" fill="none"/></svg></div>
  <div class="abs edge" style="top:684px;background:radial-gradient(circle at 5px 10px,var(--paper) 5px,transparent 5.5px) 0 0/10px 10px"></div>

  <!-- recipes -->
  <div class="abs sec-title" style="left:453px;top:737px;width:292px">Top&nbsp;<span>Recepies</span></div>
  <div class="abs divider" style="left:0;width:1200px;top:808px"><span class="rule"></span><i></i><span class="rule"></span></div>
  <p class="abs lead" style="top:842px">Perspiciatis unde omnis iste natus error sit voluptatem accusantium doloremque laudantium</p>

  <div class="abs side-btn" style="left:69px;top:1016px;border-radius:27px 0 0 27px"><svg width="12" height="14" viewBox="0 0 12 14"><path d="M8 2 3 7l5 5" stroke="#fff" stroke-width="2" fill="none"/></svg></div>
  <div class="abs side-btn" style="left:1102px;top:1016px;border-radius:0 27px 27px 0"><svg width="12" height="14" viewBox="0 0 12 14"><path d="M4 2l5 5-5 5" stroke="#fff" stroke-width="2" fill="none"/></svg></div>

  <div class="abs recipe" style="left:155px;top:907px" role="img" aria-label="Fried chicken pieces"><div class="frame"></div><div class="label">Perspiciatis unde omnis</div><div class="more"></div><div class="more-t">More</div></div>
  <div class="abs recipe" style="left:491px;top:907px;background:linear-gradient(160deg,#4a3426,#2a1a10)" role="img" aria-label="Wings with fries and dip"><div class="frame"></div><div class="label">Perspiciatis unde omnis</div><div class="more"></div><div class="more-t">More</div></div>
  <div class="abs recipe" style="left:809px;top:907px;background:linear-gradient(160deg,#b2471d,#7a2410)" role="img" aria-label="Spicy chicken wings with celery"><div class="frame"></div><div class="label">Perspiciatis unde omnis</div><div class="more"></div><div class="more-t">More</div></div>

  <!-- events -->
  <section class="abs events">
    <h2>UPCOMING <span>EVENTS</span></h2>
    <p class="sub">perspiciatis unde omnis iste natus</p>

    <div class="abs event" style="left:100px;top:138px">
      <div class="date"><b>02</b><small>December</small></div>
      <h5>LOVE IN MONTMARTRE EVENING</h5>
      <p style="top:34px"><svg width="11" height="11" viewBox="0 0 12 12"><circle cx="6" cy="6" r="5" fill="none" stroke="#fff" stroke-width="1.5"/><path d="M6 3v3h2" stroke="#fff" fill="none"/></svg>02 / 12 / 2015 &nbsp; 8.30pm - 11.00 pm</p>
      <p style="top:58px"><svg width="11" height="12" viewBox="0 0 12 14"><path d="M6 0a5 5 0 0 1 5 5c0 4-5 9-5 9S1 9 1 5a5 5 0 0 1 5-5z" fill="#fff"/></svg>Nouncing pleasure</p>
    </div>
    <div class="abs event" style="left:451px;top:138px">
      <div class="date"><b>02</b><small>December</small></div>
      <h5>LOVE IN MONTMARTRE EVENING</h5>
      <p style="top:34px"><svg width="11" height="11" viewBox="0 0 12 12"><circle cx="6" cy="6" r="5" fill="none" stroke="#fff" stroke-width="1.5"/><path d="M6 3v3h2" stroke="#fff" fill="none"/></svg>02 / 12 / 2015 &nbsp; 8.30pm - 11.00 pm</p>
      <p style="top:58px"><svg width="11" height="12" viewBox="0 0 12 14"><path d="M6 0a5 5 0 0 1 5 5c0 4-5 9-5 9S1 9 1 5a5 5 0 0 1 5-5z" fill="#fff"/></svg>Nouncing pleasure</p>
    </div>
    <div class="abs event" style="left:804px;top:138px">
      <div class="date"><b>02</b><small>December</small></div>
      <h5>LOVE IN MONTMARTRE EVENING</h5>
      <p style="top:34px"><svg width="11" height="11" viewBox="0 0 12 12"><circle cx="6" cy="6" r="5" fill="none" stroke="#fff" stroke-width="1.5"/><path d="M6 3v3h2" stroke="#fff" fill="none"/></svg>02 / 12 / 2015 &nbsp; 8.30pm - 11.00 pm</p>
      <p style="top:58px"><svg width="11" height="12" viewBox="0 0 12 14"><path d="M6 0a5 5 0 0 1 5 5c0 4-5 9-5 9S1 9 1 5a5 5 0 0 1 5-5z" fill="#fff"/></svg>Nouncing pleasure</p>
    </div>
    <div class="abs btn-outline">VIEW MORE EVENTS</div>
  </section>
  <div class="abs edge" style="top:1264px;background:radial-gradient(circle at 5px 10px,#1e1a16 5px,transparent 5.5px) 0 0/10px 10px"></div>
  <div class="abs edge" style="top:1608px;background:radial-gradient(circle at 5px 10px,var(--paper) 5px,transparent 5.5px) 0 0/10px 10px"></div>

  <!-- menu -->
  <div class="abs sec-title" style="left:446px;top:1660px;width:308px">Delicious&nbsp;<span>Menu</span></div>
  <div class="abs divider" style="left:0;width:1200px;top:1733px"><span class="rule"></span><i></i><span class="rule"></span></div>

  <div class="abs dish" style="left:100px;top:1823px"><div class="img" role="img" aria-label="Burger" style="background:radial-gradient(circle,#d59a4e,#a4541c 70%,#fff 72%)"></div></div>
  <div class="abs dish" style="left:358px;top:1785px"><div class="img" role="img" aria-label="Glazed chicken wings" style="background:radial-gradient(circle,#b25323,#7a2e10 65%,#fff 70%)"></div></div>
  <div class="abs dish" style="left:613px;top:1785px"><div class="img" role="img" aria-label="Glasses of beer" style="background:radial-gradient(circle,#f2b630,#d88d10 60%,#fff 68%)"></div></div>
  <div class="abs dish" style="left:869px;top:1785px"><div class="img" role="img" aria-label="Wings with dip on a plate" style="background:radial-gradient(circle,#cf4a22,#a8331a 55%,#eee 65%,#fff 72%)"></div></div>

  <div class="abs dish-meta" style="left:100px;top:2028px"><h6>Burgers</h6><em>Increased horsepower</em><div class="price"><s>$ 78.00</s>$ 78.00</div></div>
  <div class="abs dish-meta" style="left:358px;top:2028px"><h6>Wings</h6><em>Increased horsepower</em><div class="price">$ 78.00</div></div>
  <div class="abs dish-meta" style="left:613px;top:2028px"><h6>Beer</h6><em>Increased horsepower</em><div class="price">$ 78.00</div></div>
  <div class="abs dish-meta" style="left:869px;top:2028px"><h6>Trivia</h6><em>Increased horsepower</em><div class="price"><s>$ 78.00</s>$ 78.00</div></div>

  <div class="abs order" style="left:155px;top:2113px">Order Now</div>
  <div class="abs order" style="left:413px;top:2113px">Order Now</div>
  <div class="abs order" style="left:668px;top:2113px">Order Now</div>
  <div class="abs order" style="left:924px;top:2113px">Order Now</div>

  <!-- footer -->
  <footer class="abs footer">
    <h3 style="left:100px;top:62px">Contact Info</h3>
    <div class="c-item" style="top:100px">
      <svg width="18" height="22" viewBox="0 0 12 14"><path d="M6 0a5 5 0 0 1 5 5c0 4-5 9-5 9S1 9 1 5a5 5 0 0 1 5-5z" fill="#f28c0f"/><circle cx="6" cy="5" r="2" fill="#1d1916"/></svg>
      <div><h6>Address :</h6><p>Street Name, City Name,<br>Country Name 45867</p></div>
    </div>
    <div class="c-item" style="top:178px">
      <svg width="18" height="18" viewBox="0 0 24 24"><path d="M6.6 10.8a15 15 0 0 0 6.6 6.6l2.2-2.2c.3-.3.7-.4 1-.2 1.1.4 2.3.6 3.6.6.6 0 1 .4 1 1V20c0 .6-.4 1-1 1A17 17 0 0 1 3 4c0-.6.4-1 1-1h3.5c.6 0 1 .4 1 1 0 1.3.2 2.5.6 3.6.1.3 0 .7-.2 1z" fill="#f28c0f"/></svg>
      <div><h6>Call :</h6><p>+123 4567 890</p></div>
    </div>
    <div class="c-item" style="top:234px">
      <svg width="20" height="16" viewBox="0 0 20 16"><rect width="20" height="16" rx="2" fill="#f28c0f"/><path d="M1 2l9 7 9-7" stroke="#1d1916" stroke-width="2" fill="none"/></svg>
      <div><h6>Email :</h6><p>hello@fizzshedgrill.com</p></div>
    </div>

    <h3 style="left:377px;top:64px">Opening Hours</h3>
    <div class="hours">
      <div style="top:104px"><span>Mondays</span><span class="line"></span><span>Closed</span></div>
      <div style="top:134px"><span>Tue-Fri</span><span class="line"></span><span>10 am - 09 pm</span></div>
      <div style="top:164px"><span>Sat-Sun</span><span class="line"></span><span>08 am - 06 pm</span></div>
      <div style="top:194px"><span>Public Holidays</span><span class="line"></span><span>11 am - 06 pm</span></div>
    </div>

    <div class="abs map" role="img" aria-label="Street map showing the restaurant location"></div>

    <div class="abs foot-rule"></div>
    <p class="abs copy">© 2016 Fizz's Shed and Grill.com All rights reserved.</p>
    <div class="abs social" style="left:932px;top:335px"></div>
    <div class="abs social" style="left:968px;top:335px"></div>
    <div class="abs social" style="left:1004px;top:335px"></div>
    <div class="abs social" style="left:1040px;top:335px"></div>
    <div class="abs social" style="left:1076px;top:335px"></div>
  </footer>
  <div class="abs edge" style="top:2194px;background:radial-gradient(circle at 5px 10px,#1d1916 5px,transparent 5.5px) 0 0/10px 10px"></div>

</div>
</body>
</html>
```